Android Payment Application UI Design

We require a UI/UX design for an existing Android card-based payment application.

We're looking to improve the look + feel of the existing app. What we're after:
- Colour palette options
- Fonts
- Icons

See attached document for existing screen types, icons, etc.

All resources provided must be royalty free.

It's to run on a specialised device, with 720 x 1280 pixel resolution, in portrait only (landscape not required).

Please provide mockup examples of the new screen layout applied to the existing screens in the document.

Target Market(s)

Retail business users

Font styles to use
Sans Serif

Colors

Designer to choose colors to be used in the design.

Requirements
Must have
• Looking for
• - modern design
• - simple colours, easy-to-read sans-serif fonts
• - cohesive, consistent design between screens

```html
<!DOCTYPE html>
<html lang="en">
<head>
<meta charset="utf-8">
<title>Sale – Enter Amount</title>
<link href="https://fonts.googleapis.com/css2?family=Lato:wght@400;700;900&display=swap" rel="stylesheet">
<style>
  :root {
    --status-navy: #0e2a66;
    --status-navy-dark: #0a1f4d;
    --header-bg: #ffffff;
    --logo-blue: #1b5fa8;
    --icon-grey: #4a4f5c;
    --panel-top: #ffffff;
    --panel-bottom: #c5e3f3;
    --title-ink: #2b2f3d;
    --field-bg: #ffffff;
    --field-border: #d7dde4;
    --field-hint: #8a8f98;
    --keypad-bg: #1690d4;
    --keypad-bg-light: #2aa2e2;
    --key-bg: #ffffff;
    --key-bg-shade: #e6e9ee;
    --key-ink: #3a3e49;
    --cancel: #ec2f2b;
    --delete: #f8a023;
    --done: #4ea02a;
    --done-dark: #3d8a1f;
  }
  * { box-sizing: border-box; margin: 0; padding: 0; }
  html, body { width: 675px; height: 1200px; overflow: hidden; }
  body { font-family: "Lato", Arial, sans-serif; background: #ffffff; position: relative; }

  .status-bar {
    position: absolute; left: 0; top: 0; width: 675px; height: 61px;
    background: linear-gradient(180deg, var(--status-navy), var(--status-navy-dark));
    color: #ffffff; font-size: 22px;
  }
  .status-bar .carrier { position: absolute; left: 16px; top: 16px; display: flex; align-items: center; gap: 8px; }
  .status-bar .signal { display: flex; gap: 3px; }
  .status-bar .signal i { width: 10px; height: 10px; border-radius: 50%; background: #fff; display: block; }
  .status-bar .signal i.off { background: transparent; border: 1.5px solid #fff; }
  .status-bar .time { position: absolute; left: 0; right: 0; top: 16px; text-align: center; }
  .status-bar .battery { position: absolute; right: 16px; top: 16px; display: flex; align-items: center; gap: 10px; }

  .app-header {
    position: absolute; left: 0; top: 61px; width: 675px; height: 119px;
    background: var(--header-bg); border-bottom: 1px solid #e4e8ee;
  }
  .app-header .menu-data { position: absolute; left: 14px; top: 40px; }
  .app-header .menu-list { position: absolute; right: 16px; top: 42px; }
  .brand {
    position: absolute; left: 0; right: 0; top: 36px;
    display: flex; justify-content: center; align-items: center; gap: 12px;
    color: var(--logo-blue); font-weight: 900; font-size: 40px; letter-spacing: 1px;
  }
  .brand .dot { width: 36px; height: 36px; border-radius: 50%; background: var(--logo-blue); }

  .entry-panel {
    position: absolute; left: 0; top: 180px; width: 675px; height: 612px;
    background: linear-gradient(180deg, var(--panel-top) 0%, #eef7fc 40%, var(--panel-bottom) 100%);
    text-align: center; color: var(--title-ink);
  }
  .entry-panel h1 { position: absolute; left: 0; right: 0; top: 182px; font-size: 45px; font-weight: 700; }
  .entry-panel h2 { position: absolute; left: 0; right: 0; top: 240px; font-size: 32px; font-weight: 700; }
  .amount-field {
    position: absolute; left: 85px; top: 320px; width: 406px; height: 88px;
    background: var(--field-bg); border: 2px solid var(--field-border); border-radius: 12px;
    text-align: left; padding: 31px 0 0 30px; font-size: 16px; color: var(--field-hint);
  }
  .currency { position: absolute; left: 524px; top: 344px; font-size: 34px; font-weight: 700; }

  .keypad {
    position: absolute; left: 0; top: 792px; width: 675px; height: 408px;
    background: linear-gradient(180deg, var(--keypad-bg-light), var(--keypad-bg));
  }
  .key {
    position: absolute; width: 138px; height: 68px;
    background: linear-gradient(180deg, var(--key-bg), var(--key-bg-shade));
    border-radius: 4px; box-shadow: 0 3px 4px rgba(0, 40, 80, .35);
    display: flex; align-items: center; justify-content: center;
    font-size: 30px; color: var(--key-ink);
  }
  .col-1 { left: 31px; } .col-2 { left: 187px; } .col-3 { left: 342px; } .col-4 { left: 500px; width: 141px; }
  .row-1 { top: 54px; } .row-2 { top: 140px; } .row-3 { top: 225px; } .row-4 { top: 311px; }
  .key.action { color: #ffffff; font-size: 18px; font-weight: 400; }
  .key.cancel { background: var(--cancel); }
  .key.delete { background: var(--delete); }
  .key.done { background: linear-gradient(180deg, var(--done), var(--done-dark)); height: 154px; font-weight: 700; }
</style>
</head>
<body>
  <div class="status-bar">
    <div class="carrier">
      <span class="signal"><i></i><i></i><i></i><i></i><i class="off"></i></span>
      <span>Carrier</span>
      <svg width="16" height="20" viewBox="0 0 16 20"><rect x="1" y="1" width="14" height="18" rx="2" fill="none" stroke="#fff" stroke-width="2"/><rect x="4" y="5" width="8" height="10" fill="#fff"/></svg>
    </div>
    <div class="time">11:49 AM</div>
    <div class="battery">
      <span>2%</span>
      <svg width="40" height="20" viewBox="0 0 40 20"><rect x="1" y="1" width="34" height="18" rx="3" fill="none" stroke="#fff" stroke-width="2"/><rect x="36" y="6" width="3" height="8" fill="#fff"/><path d="M20 3 L12 11 H18 L15 17 L24 8 H18 Z" fill="#fff"/></svg>
    </div>
  </div>

  <header class="app-header">
    <svg class="menu-data" width="24" height="36" viewBox="0 0 24 36" fill="var(--icon-grey)">
      <ellipse cx="12" cy="5" rx="11" ry="4"/>
      <path d="M1 9 Q12 15 23 9 V15 Q12 21 1 15 Z"/>
      <path d="M1 19 Q12 25 23 19 V25 Q12 31 1 25 Z"/>
    </svg>
    <div class="brand"><span class="dot"></span><span>ZELVORA</span></div>
    <svg class="menu-list" width="30" height="28" viewBox="0 0 30 28" fill="var(--icon-grey)">
      <circle cx="3" cy="4" r="3"/><rect x="9" y="2" width="21" height="4"/>
      <circle cx="3" cy="14" r="3"/><rect x="9" y="12" width="21" height="4"/>
      <circle cx="3" cy="24" r="3"/><rect x="9" y="22" width="21" height="4"/>
    </svg>
  </header>

  <main class="entry-panel">
    <h1>SALE</h1>
    <h2>PLEASE ENTER AMOUNT</h2>
    <div class="amount-field">0.00</div>
    <div class="currency">GBP</div>
  </main>

  <section class="keypad">
    <div class="key col-1 row-1">1</div>
    <div class="key col-2 row-1">2</div>
    <div class="key col-3 row-1">3</div>
    <div class="key col-4 row-1 action cancel">CANCEL</div>
    <div class="key col-1 row-2">4</div>
    <div class="key col-2 row-2">5</div>
    <div class="key col-3 row-2">6</div>
    <div class="key col-4 row-2 action delete">DEL</div>
    <div class="key col-1 row-3">7</div>
    <div class="key col-2 row-3">8</div>
    <div class="key col-3 row-3">9</div>
    <div class="key col-4 row-3 action done">DONE</div>
    <div class="key col-1 row-4">00</div>
    <div class="key col-2 row-4">0</div>
    <div class="key col-3 row-4">000</div>
  </section>
</body>
</html>
```